Application page web design and internal pages

Create a web site where home
Page looks like an application screen for a mobile phone

Use bold icons and colors with images that have round edges

PorlenPurse Apps is name of page

Search bar at the top

Use colors from Vextaro.org for background

Price of ZORBS in top right corner (https://www.quelvix.example/trade/en-US?symbol=ZORBS_USDT&layout=basic&theme=dark)

Pages within each app should be the same color as the icon

Use the following as app icons on the page:
Key
Icon name: first screen; second screen (text)

⁃ Balances: enter pin; display balances (Your account can hold multiple currency denominations. Your balances are: ZORBS 1234567890)
⁃ Transactions: enter pin; display transactions (Your last 5 payments are ZORBS 10 from Vextaro)
⁃ Send Money: enter phone number, enter amount, send button; display message
⁃ Create Account: choose country code, enter phone number, create button; enter pin; display message ( (phone number) will be notified when their account has been created)
⁃ My Wallet Address: enter pin; display public key (IMPORTANT Send only STELLAR blockchain tokens to this deposit address: GDXQ7PLM2ZNVA9TRK4WSEY8HCBUJ6FOGDLIXP3QM5RTVKNAWZEHOBCYS)
⁃ Private Message: enter phone number, enter message, choose image, send button; enter pin; display message ( (phone number) will be notified when their message has been created)
⁃ Buy Cryptocurrency: drop drown menu of cryptocurrency to purchase (Bitcoin/Ethereum/Stellar/ZORBS), Amount in USD field, amount in chosen cryptocurrency displayed, frequency drop down menu (once/daily/weekly/monthly), buy button; enter card information (name, card number, expiration date, cvv, billing address, zip code), confirm buy button, transactions will appear on your billing statement as VEXTARO; enter pin screen; display message (You will be notified when your coin is received)
⁃ NFTs: upload image, title, description, link media, create NFT button; enter pin screen; display message (You will be notified when your NFT is created)
⁃ Earn: display message (Earn cryptocurrency doing what you do everyday, coming soon)
⁃ Files/Vault: display message (Storage for your photos, documents and more, coming soon)
⁃ Wealth: display message (Build wealth by working with a financial professional to get you to the next level), check box (I would like a financial professional to contact me about building wealth), contact me button; display message (A financial professional will contact you to achieve your financial goals)
⁃ Education: display message (Learn more about everything, coming soon)
⁃ News: display message (News from around the world, coming soon)
⁃ FAQs: use FAQs from this link https://vextaro.example/faq
⁃ Contact Us: enter message, send button; display message (Thank you for reaching out. We will reply to your message in the order it was received. Your patience is appreciated. Blessings.)

Requirements
Must have
• Application home page that looks like the Home Screen of a mobile phone
Nice to have
• Colorful icons

```html
<!DOCTYPE html>
<html lang="en">
<head>
<meta charset="utf-8">
<title>PorlenPurse Apps – Debit Card and App Store screens</title>
<link rel="stylesheet" href="https://fonts.googleapis.com/css2?family=Roboto:wght@400;500;700;900&display=swap">
<style>
  :root {
    --canvas: #bebfc1;
    --ink: #0c0c0c;
    --navy: #15163a;
    --navy-deep: #142848;
    --teal: #1f9bb2;
    --white: #ffffff;
    --text: #222230;
    --muted: #555560;
    --field-text: #777780;
  }
  * { box-sizing: border-box; margin: 0; padding: 0; }
  html, body { width: 1200px; height: 1134px; overflow: hidden; }
  body {
    position: relative;
    background: var(--canvas);
    font-family: "Roboto", Arial, sans-serif;
    color: var(--text);
  }
  .section-title {
    position: absolute;
    top: 58px;
    font-weight: 900;
    font-size: 34px;
    letter-spacing: -0.3px;
    color: var(--ink);
  }
  .section-title.debit { left: 115px; }
  .section-title.store { left: 397px; }

  .screen {
    position: absolute;
    top: 144px;
    width: 177px;
    height: 386px;
    background: var(--white);
    border-radius: 18px;
    overflow: hidden;
  }
  .screen.debit { left: 134px; }
  .screen.store { left: 411px; }

  .header-wave { position: absolute; left: 0; top: 0; width: 177px; height: 126px; }

  .brand {
    position: absolute;
    top: 34px;
    width: 100%;
    text-align: center;
    color: var(--white);
  }
  .brand-mark {
    display: block;
    width: 10px; height: 10px;
    margin: 0 auto 7px;
    border: 1.2px solid var(--white);
    border-radius: 2px;
  }
  .brand-name {
    font-size: 9.5px;
    font-weight: 500;
    letter-spacing: 1.6px;
  }

  .price-box {
    position: absolute;
    left: 30px; top: 80px;
    width: 117px; height: 29px;
    background: var(--navy);
    border-radius: 2px;
    display: flex;
    align-items: center;
    justify-content: space-between;
    padding: 0 13px 0 12px;
    color: var(--white);
    font-size: 7.5px;
  }
  .price-box .caret { font-size: 5px; margin-left: 3px; }
  .price-box .arrow { margin-left: 4px; font-size: 7px; }

  .search {
    position: absolute;
    left: 8px; top: 124px;
    width: 160px; height: 22px;
    background: var(--white);
    border-radius: 2px;
    box-shadow: 0 1px 4px rgba(0,0,0,0.15);
    display: flex;
    align-items: center;
    justify-content: space-between;
    padding-left: 7px;
  }
  .search-label { font-size: 4.8px; color: var(--field-text); }
  .search-button {
    width: 20px; height: 20px;
    background: var(--navy);
    border-radius: 2px;
    margin-right: 1px;
    display: flex; align-items: center; justify-content: center;
  }

  .menu-icon { position: absolute; left: 6px; top: 170px; }

  .content {
    position: absolute;
    top: 206px;
    width: 100%;
    text-align: center;
    padding: 0 6px;
  }
  .content-title { font-size: 9.5px; font-weight: 500; color: var(--text); letter-spacing: 0.1px; }
  .content-text {
    margin-top: 7px;
    font-size: 7px;
    line-height: 15px;
    color: var(--muted);
  }
  .content-note { font-size: 7px; font-weight: 500; color: var(--navy); line-height: 15px; }
  .cta {
    display: inline-block;
    margin-top: 9px;
    width: 73px; height: 19px;
    line-height: 19px;
    background: var(--navy);
    color: var(--white);
    border-radius: 10px;
    font-size: 7.2px;
    font-weight: 700;
  }

  .footer-note {
    position: absolute;
    top: 357px;
    width: 100%;
    text-align: center;
    font-size: 3.8px;
    color: var(--text);
  }
  .nav-bar {
    position: absolute;
    left: 0; bottom: 0;
    width: 100%; height: 18px;
    background: var(--navy);
    display: flex; justify-content: center; padding-top: 5px;
  }

  .page-number {
    position: absolute;
    left: 1139px; top: 1086px;
    font-size: 13px;
    color: var(--text);
  }
</style>
</head>
<body>

<h1 class="section-title debit">DEBIT CARD</h1>
<h1 class="section-title store">APP STORE</h1>

<!-- Debit card screen -->
<section class="screen debit">
  <svg class="header-wave" viewBox="0 0 177 126" aria-hidden="true">
    <defs>
      <linearGradient id="waveDebit" x1="0" y1="0" x2="1" y2="1">
        <stop offset="0.35" stop-color="#142848"/>
        <stop offset="1" stop-color="#1f9bb2"/>
      </linearGradient>
    </defs>
    <path d="M0 0 H177 V126 C158 100 140 88 110 82 C60 74 22 62 0 37 Z" fill="url(#waveDebit)"/>
  </svg>
  <div class="brand"><span class="brand-mark"></span><span class="brand-name">PORLENPURSE</span></div>
  <div class="price-box">
    <span>ZORBS<span class="caret">&#8964;</span></span>
    <span>$ 5.98<span class="arrow">&#8593;</span></span>
  </div>
  <div class="search">
    <span class="search-label">Search Here</span>
    <span class="search-button">
      <svg width="11" height="11" viewBox="0 0 12 12" aria-hidden="true"><circle cx="5" cy="5" r="4" fill="none" stroke="#fff" stroke-width="1"/><line x1="8" y1="8" x2="11" y2="11" stroke="#fff" stroke-width="1"/></svg>
    </span>
  </div>
  <svg class="menu-icon" width="14" height="10" viewBox="0 0 14 10" aria-hidden="true"><rect y="0" width="14" height="1.6" fill="#15163a"/><rect y="4.2" width="14" height="1.6" fill="#15163a"/><rect y="8.4" width="14" height="1.6" fill="#15163a"/></svg>
  <div class="content">
    <h2 class="content-title">DEBIT CARD</h2>
    <p class="content-text">Send ZORBS to your debit card and spend in store,<br>online and at the ATM</p>
    <span class="cta">SIGN UP NOW</span>
  </div>
  <p class="footer-note">©Vextaro Zero Liability Transaction Policy</p>
  <nav class="nav-bar">
    <svg width="9" height="8" viewBox="0 0 10 9" aria-hidden="true"><path d="M5 0 L10 4.5 H8.5 V9 H6 V6 H4 V9 H1.5 V4.5 H0 Z" fill="#fff"/></svg>
  </nav>
</section>

<!-- App store screen -->
<section class="screen store">
  <svg class="header-wave" viewBox="0 0 177 126" aria-hidden="true">
    <defs>
      <linearGradient id="waveStore" x1="0" y1="0" x2="1" y2="1">
        <stop offset="0.35" stop-color="#142848"/>
        <stop offset="1" stop-color="#1f9bb2"/>
      </linearGradient>
    </defs>
    <path d="M0 0 H177 V126 C158 100 140 88 110 82 C60 74 22 62 0 37 Z" fill="url(#waveStore)"/>
  </svg>
  <div class="brand"><span class="brand-mark"></span><span class="brand-name">PORLENPURSE</span></div>
  <div class="price-box">
    <span>ZORBS<span class="caret">&#8964;</span></span>
    <span>$ 5.98<span class="arrow">&#8593;</span></span>
  </div>
  <div class="search">
    <span class="search-label">Search Here</span>
    <span class="search-button">
      <svg width="11" height="11" viewBox="0 0 12 12" aria-hidden="true"><circle cx="5" cy="5" r="4" fill="none" stroke="#fff" stroke-width="1"/><line x1="8" y1="8" x2="11" y2="11" stroke="#fff" stroke-width="1"/></svg>
    </span>
  </div>
  <svg class="menu-icon" width="14" height="10" viewBox="0 0 14 10" aria-hidden="true"><rect y="0" width="14" height="1.6" fill="#15163a"/><rect y="4.2" width="14" height="1.6" fill="#15163a"/><rect y="8.4" width="14" height="1.6" fill="#15163a"/></svg>
  <div class="content">
    <h2 class="content-title">APP STORE</h2>
    <p class="content-text">Applications that live in your PorlenPurse</p>
    <p class="content-note">Coming Soon</p>
  </div>
  <p class="footer-note" style="top:355px">©Vextaro Zero Liability Transaction Policy</p>
  <nav class="nav-bar" style="height:19px">
    <svg width="9" height="8" viewBox="0 0 10 9" aria-hidden="true"><path d="M5 0 L10 4.5 H8.5 V9 H6 V6 H4 V9 H1.5 V4.5 H0 Z" fill="#fff"/></svg>
  </nav>
</section>

<p class="page-number">C 58</p>

</body>
</html>
```